Brellwick Partners, LLC Stationary

Brellwick Partners, LLC is a new financial planning and consulting company. We are looking for designs on business cards, letterhead, envelopes, and anything else that would be useful. Our preference for business card design is two sided. We are looking for a professional and clean look with incorporating the logo and patriotic feel. Thank you to all who participate and good luck!

```html
<!DOCTYPE html>
<html lang="en">
<head>
<meta charset="utf-8">
<title>Brellwick Partners, LLC – Business Card</title>
<link href="https://fonts.googleapis.com/css2?family=Montserrat:wght@400;600&family=Open+Sans:wght@400;600&display=swap" rel="stylesheet">
<style>
  :root {
    --backdrop: #d9d6d3;
    --card: #151515;
    --card-edge: #222;
    --blue: #2c6bb5;
    --red: #d42a2a;
    --white: #f2f2f2;
    --grey: #8a8a8a;
    --rule: #5a5a5a;
  }
  * { margin: 0; padding: 0; box-sizing: border-box; }
  html, body { width: 1200px; height: 814px; overflow: hidden; }
  body {
    background: var(--backdrop);
    font-family: "Open Sans", Arial, sans-serif;
    position: relative;
  }
  .card {
    position: absolute;
    top: 258px;
    width: 520px;
    height: 298px;
    background: var(--card);
    border: 1px solid var(--card-edge);
    border-radius: 4px;
    box-shadow: 0 10px 28px rgba(0,0,0,.28);
  }
  .card--back { left: 50px; }
  .card--front { left: 630px; }

  /* back side */
  .brand {
    position: absolute;
    left: 36px;
    top: 118px;
    width: 210px;
  }
  .brand-name {
    display: flex;
    align-items: center;
    gap: 10px;
    font-family: "Montserrat", Arial, sans-serif;
    font-weight: 600;
    font-size: 19px;
    letter-spacing: .5px;
    color: var(--blue);
    line-height: 1.15;
  }
  .brand-dot {
    width: 14px; height: 14px; border-radius: 50%;
    background: var(--red);
    flex: none;
  }
  .brand-tagline {
    margin-top: 8px;
    padding-left: 24px;
    font-family: "Montserrat", Arial, sans-serif;
    font-size: 7px;
    letter-spacing: 1px;
    text-transform: uppercase;
    color: var(--grey);
  }
  .divider {
    position: absolute;
    left: 270px;
    top: 40px;
    width: 1px;
    height: 210px;
    background: var(--rule);
  }
  .contact {
    position: absolute;
    left: 290px;
    top: 40px;
    color: var(--white);
    font-size: 13px;
    line-height: 19px;
  }
  .contact-name { color: var(--blue); font-size: 16px; font-weight: 600; }
  .contact-role { color: var(--red); font-size: 13px; margin-bottom: 6px; }
  .contact-line { display: flex; align-items: center; gap: 7px; }
  .contact-line svg { width: 11px; height: 11px; fill: var(--blue); flex: none; }

  /* front side */
  .front-brand {
    position: absolute;
    left: 0; right: 0;
    top: 104px;
    text-align: center;
  }
  .front-name {
    display: inline-flex;
    align-items: center;
    gap: 14px;
    font-family: "Montserrat", Arial, sans-serif;
    font-weight: 600;
    font-size: 28px;
    letter-spacing: 1px;
    color: var(--white);
  }
  .front-square { width: 18px; height: 18px; background: var(--white); flex: none; }
  .front-tagline {
    margin-top: 8px;
    font-family: "Montserrat", Arial, sans-serif;
    font-size: 8px;
    letter-spacing: 2px;
    text-transform: uppercase;
    color: var(--grey);
  }
  .front-web {
    position: absolute;
    left: 0; right: 0;
    top: 222px;
    text-align: center;
    font-size: 11px;
    letter-spacing: 4px;
    color: var(--white);
  }
</style>
</head>
<body>

<section class="card card--back">
  <div class="brand">
    <div class="brand-name"><span class="brand-dot"></span>Brellwick Partners, LLC</div>
    <div class="brand-tagline">Financial Planning and Consulting</div>
  </div>
  <div class="divider"></div>
  <div class="contact">
    <div class="contact-name">Daniel Harlow</div>
    <div class="contact-role">CEO/Founder</div>
    <div>4120 Birchwood Court</div>
    <div>Fairbanks, Alaska 99701</div>
    <div class="contact-line">
      <svg viewBox="0 0 24 24"><path d="M6.6 10.8a15 15 0 0 0 6.6 6.6l2.2-2.2c.3-.3.7-.4 1-.2 1.1.4 2.3.6 3.6.6.6 0 1 .4 1 1V20c0 .6-.4 1-1 1A17 17 0 0 1 3 4c0-.6.4-1 1-1h3.5c.6 0 1 .4 1 1 0 1.3.2 2.5.6 3.6.1.3 0 .7-.2 1z"/></svg>
      555 214 7731
    </div>
    <div class="contact-line">
      <svg viewBox="0 0 24 24"><rect x="6" y="1" width="12" height="22" rx="2"/></svg>
      555 309 6624
    </div>
    <div class="contact-line">
      <svg viewBox="0 0 24 24"><path d="M2 5h20v14H2z M2 5l10 8 10-8" /></svg>
      info@brellwick.com
    </div>
    <div class="contact-line">
      <svg viewBox="0 0 24 24"><circle cx="12" cy="12" r="11"/></svg>
      www.brellwick.com
    </div>
  </div>
</section>

<section class="card card--front">
  <div class="front-brand">
    <div class="front-name"><span class="front-square"></span>Brellwick Partners, LLC</div>
    <div class="front-tagline">Financial Planning and Consulting</div>
  </div>
  <div class="front-web">www.brellwick.com</div>
</section>

</body>
</html>
```